Business Card for Coastal Tundrabridge Advisory

We need a business card for Coastal Tundrabridge Advisory. The company website address is provided below. The company logo is attached. We provide specialized permafrost services to the mining, transportation, and oil & gas industries. The card should be prepared for:
Matthias Korhonen, PhD.
Coastal Tundrabridge Advisory
PO Box 418259
Quillwater, Alaska 99642
Direct: +1-907-555-0143
Email: mkorhonen@tundrabridgeadvisory.example
Website: www.coastaltundrabridgeadvisory.example

```html
<!DOCTYPE html>
<html lang="en">
<head>
<meta charset="utf-8">
<title>Coastal Tundrabridge Advisory – Business Card</title>
<link href="https://fonts.googleapis.com/css2?family=Arimo:wght@400;700&display=swap" rel="stylesheet">
<style>
  :root {
    --backdrop: #dcdcdc;
    --card-light: #f7f7f7;
    --card-dark: #0f1720;
    --ink: #121a22;
    --ink-soft: #555b61;
    --rule: #9aa0a5;
    --paper-white: #ffffff;
  }
  * { margin: 0; padding: 0; box-sizing: border-box; }
  html, body {
    width: 1200px; height: 1040px; overflow: hidden;
    background: var(--backdrop);
    font-family: "Arimo", Arial, sans-serif;
    color: var(--ink);
  }
  .card {
    position: absolute;
    width: 644px; height: 366px;
    border-radius: 18px;
    left: 284px;
    box-shadow: 0 3px 6px rgba(0,0,0,0.25);
  }
  .card-front { top: 130px; background: var(--card-light); }
  .card-back { top: 568px; background: var(--card-dark); color: var(--paper-white); }

  .wordmark {
    position: absolute;
    text-align: center;
    font-weight: 700;
    text-transform: uppercase;
    line-height: 1.25;
  }
  .card-front .wordmark {
    left: 30px; width: 226px; top: 164px;
    font-size: 15px; letter-spacing: 2px;
    color: var(--ink);
  }
  .divider {
    position: absolute;
    left: 272px; top: 96px;
    width: 1px; height: 174px;
    background: var(--rule);
  }
  .details {
    position: absolute;
    left: 290px; top: 98px;
  }
  .person-name { font-size: 22px; font-weight: 700; line-height: 1.2; }
  .person-name .credential { font-size: 18px; }
  .person-title { font-size: 16px; color: var(--ink-soft); margin-left: 2px; line-height: 1.2; }
  .address { margin-top: 12px; font-size: 16px; line-height: 20px; }
  .contacts { list-style: none; margin-top: 12px; font-size: 15.5px; line-height: 20px; }
  .contacts li { display: flex; align-items: center; gap: 8px; }
  .contacts svg { width: 14px; height: 14px; flex: none; fill: var(--ink); }

  .card-back .wordmark {
    left: 0; right: 0; top: 136px;
    font-size: 38px; letter-spacing: 4px;
    color: var(--paper-white);
  }
</style>
</head>
<body>
  <section class="card card-front">
    <div class="wordmark">Coastal Tundrabridge<br>Advisory</div>
    <div class="divider"></div>
    <div class="details">
      <h1 class="person-name">Matthias Korhonen, <span class="credential">PhD.</span></h1>
      <p class="person-title">President</p>
      <p class="address">PO Box 418259<br>Quillwater, Alaska 99642</p>
      <ul class="contacts">
        <li>
          <svg viewBox="0 0 24 24" aria-hidden="true"><path d="M6.6 10.8a15.1 15.1 0 0 0 6.6 6.6l2.2-2.2c.3-.3.7-.4 1-.2 1.1.4 2.3.6 3.6.6.6 0 1 .4 1 1V20c0 .6-.4 1-1 1C10.6 21 3 13.4 3 4c0-.6.4-1 1-1h3.5c.6 0 1 .4 1 1 0 1.3.2 2.5.6 3.6.1.3 0 .7-.2 1z"/></svg>
          +1-907-555-0143
        </li>
        <li>
          <svg viewBox="0 0 24 24" aria-hidden="true"><path d="M2 5h20v14H2z M3.5 6.5 12 12l8.5-5.5" fill="none" stroke="#121a22" stroke-width="0"/><path d="M2 6l10 6.5L22 6v13H2z M2 5h20L12 11z"/></svg>
          mkorhonen@tundrabridgeadvisory.example
        </li>
        <li>
          <svg viewBox="0 0 24 24" aria-hidden="true"><circle cx="12" cy="12" r="10"/><path d="M8 6c2 1 3 3 1.5 4.5S8 14 10 15s1 4 0 5M15 4c-1 2 1 3 2.5 3.5s2 3 .5 4.5-1 3 1 3" fill="none" stroke="#f7f7f7" stroke-width="1.6"/></svg>
          www.coastaltundrabridgeadvisory.example
        </li>
      </ul>
    </div>
  </section>

  <section class="card card-back">
    <div class="wordmark">Coastal Tundrabridge<br>Advisory</div>
  </section>
</body>
</html>
```